Custom Cabinet Shop Needs a website design

Hi,
We need a website for a Custom Cabinet Shop and Cabinet parts manufacturing business.
The business has two sides to it. One side provides custom Kitchens, vanities, entertainment units, offices and what not to homeowners and contractors.
The 2nd side of the business provides built to order cabinet boxes and other parts required to put together a project to other cabinet shops, small contractors looking to install there own cabinets.
Website will need a Gallery to display work.
Color scheme to go well with logo.
current website is www.brambleoakcustomcabinets.com
being changed to www.brambleoak.ca
Logo Included in attached files.
Tagline "Joinery with Spirit"
Mission Statement "Our passion is to deliver inspired cabinetry solutions to suit all your needs, supported by our phenomenal star class customer service"
The website should convey quality and professionalism.
Thank you.
Homeowners/ Contractors
Entertainment

```html
<!DOCTYPE html>
<html lang="en">
<head>
<meta charset="utf-8">
<title>Brambleoak Custom Cabinets</title>
<link href="https://fonts.googleapis.com/css2?family=Exo:wght@400;500;600&family=Open+Sans:ital,wght@0,400;0,600;0,700;1,400&display=swap" rel="stylesheet">
<style>
:root{
  --orange:#f15a22;
  --dark:#1e1c1c;
  --footer:#282626;
  --ink:#3a3a3a;
  --muted:#777;
  --line:#cfcfcf;
  --white:#ffffff;
}
*{margin:0;padding:0;box-sizing:border-box}
html,body{width:758px;height:1200px;overflow:hidden;background:var(--white)}
body{position:relative;font-family:"Open Sans",sans-serif;color:var(--ink)}
.abs{position:absolute}

/* hero */
.hero{left:0;top:0;width:758px;height:337px;overflow:hidden}
.hero-photo{position:absolute;inset:0;background:
  radial-gradient(ellipse at 55% 70%,#5a5048 0%,#3a342f 40%,#1f1c1a 100%),#2a2623}
.hero-photo::after{content:"";position:absolute;inset:0;background:linear-gradient(90deg,rgba(0,0,0,.25),rgba(0,0,0,0) 40%,rgba(255,255,255,.06) 85%,rgba(0,0,0,.2))}
.hero-phone{right:118px;top:8px;color:var(--white);font-family:"Exo",sans-serif;font-size:8.5px;display:flex;align-items:center;gap:4px}
.hero-title{left:0;width:758px;top:84px;text-align:center;color:var(--white);font-family:"Exo",sans-serif;font-weight:500;font-size:28px;letter-spacing:1px;text-transform:uppercase}
.hero-sub{left:0;width:758px;top:118px;text-align:center;color:#e6e6e6;font-size:7.2px}
.hero-social{left:330px;top:147px;display:flex;gap:8px}
.hero-cta{left:322px;top:200px;width:115px;height:24px}
.hero-cta span{position:absolute;inset:0;display:flex;align-items:center;justify-content:center;color:var(--white);font-size:8.5px;font-weight:400}
.hero-more{left:349px;top:237px;color:#ddd;font-size:7.4px;display:flex;align-items:center;gap:5px;letter-spacing:.4px}
.hero-arrow{top:150px}

/* nav */
.nav{left:0;top:337px;width:758px;height:47px;border-bottom:1px solid #d6d6d6;background:var(--white)}
.brand{left:112px;top:15px;display:flex;align-items:center;gap:6px;font-family:"Exo",sans-serif;font-weight:600;font-size:13px;color:var(--dark);letter-spacing:.3px}
.brand i{display:block;width:11px;height:11px;background:var(--orange)}
.menu{left:380px;top:0;height:46px;display:flex;list-style:none;font-size:7px;font-weight:400;color:var(--dark)}
.menu li{height:46px;display:flex;align-items:center;padding:0 6px}
.menu li.active{background:var(--dark);color:var(--white);padding:0 7px}
.nav-pin{left:637px;top:16px}

/* services */
.section-title{left:0;width:758px;top:427px;text-align:center;font-family:"Exo",sans-serif;font-weight:500;font-size:24px;color:var(--orange)}
.title-rule{top:442px;height:1px;background:var(--line)}
.section-sub{left:0;width:758px;top:459px;text-align:center;font-size:7px;font-style:italic;color:#444}
.worker{left:0;top:528px;width:220px;height:442px;background:linear-gradient(180deg,#f7f7f7 0%,#e7e9ec 35%,#c9d3de 60%,#d9c9ac 85%,#f4f4f4 100%)}
.service-icon{width:58px;height:58px}
.service{width:124px}
.service h2{font-size:10.4px;font-weight:700;color:var(--orange);margin-bottom:6px;white-space:nowrap}
.service p{font-size:6.3px;line-height:1.25;color:#444;margin-bottom:6px}
.service ul{list-style:none}
.service li{font-size:6.3px;line-height:1.25;color:#444;margin-bottom:6.5px;padding-left:10px;position:relative}
.service li svg{position:absolute;left:0;top:1px}
.btn{display:flex;align-items:center;justify-content:center;height:17px;background:var(--dark);color:var(--white);font-size:6.4px}

/* mission + gallery */
.mission{left:142px;top:778px;width:230px;height:111px;background:var(--orange);color:var(--white);padding:17px 8px 0 19px;overflow:hidden}
.mission h3{font-weight:400;font-size:13px;line-height:16px;margin-bottom:4px}
.mission p{font-size:10.4px;line-height:13.3px}
.gallery{left:381px;top:778px;width:235px;display:grid;grid-template-columns:repeat(3,76px);gap:4px 3.5px}
.gallery div{height:53px}

/* footer */
.footer{left:0;top:970px;width:758px;height:230px;background:var(--footer);color:#bdbdbd;text-align:center}
.footer .pin{position:absolute;left:372px;top:54px}
.footer .addr{position:absolute;left:0;width:758px;top:78px;font-size:6.4px}
.footer .tel{position:absolute;left:0;width:758px;top:88px;font-size:8px}
.footer .social{position:absolute;left:355px;top:105px;display:flex;gap:2px}
.footer .copy{position:absolute;left:0;width:758px;top:137px;font-size:6.4px}
.footer .rule{position:absolute;left:142px;top:158px;width:474px;height:1px;background:#3e3c3c}
.footer-menu{position:absolute;left:0;width:758px;top:165px;display:flex;justify-content:center;gap:7px;list-style:none;font-size:6px;color:#9a9a9a;padding-left:4px}
</style>
</head>
<body>

<header class="hero abs">
  <div class="hero-photo" role="img" aria-label="Photo of a dark wood kitchen with granite island and bar stools"></div>
  <div class="hero-phone abs">
    <svg width="7" height="7" viewBox="0 0 10 10"><path d="M2 0.5 L3.8 2.6 L2.9 3.8 Q4 6 6.2 7.1 L7.4 6.2 L9.5 8 L8.3 9.5 Q3.5 9 0.5 1.7Z" fill="#fff"/></svg>
    555-010-4821
  </div>
  <h1 class="hero-title abs">Joinery with Spirit</h1>
  <p class="hero-sub abs">Lorem ipsum dolor sit amet, consectetur adipisicing elit, sed do eiusmod tempor incididunt</p>
  <div class="hero-social abs">
    <svg width="28" height="30" viewBox="0 0 28 30"><polygon points="14,1 27,8 27,22 14,29 1,22 1,8" fill="none" stroke="#fff" stroke-width="1"/></svg>
    <svg width="28" height="30" viewBox="0 0 28 30"><polygon points="14,1 27,8 27,22 14,29 1,22 1,8" fill="none" stroke="#fff" stroke-width="1"/></svg>
    <svg width="28" height="30" viewBox="0 0 28 30"><polygon points="14,1 27,8 27,22 14,29 1,22 1,8" fill="none" stroke="#fff" stroke-width="1"/></svg>
  </div>
  <div class="hero-cta abs">
    <svg width="115" height="24" viewBox="0 0 115 24"><polygon points="0,0 115,0 109,12 115,24 0,24 6,12" fill="#f15a22"/></svg>
    <span>CALL TO ACTION</span>
  </div>
  <div class="hero-more abs">
    <svg width="8" height="8" viewBox="0 0 10 10"><circle cx="5" cy="5" r="5" fill="#fff"/><path d="M4 2.8 L6.2 5 L4 7.2" fill="none" stroke="#2a2623" stroke-width="1.3"/></svg>
    Learn More
  </div>
  <svg class="hero-arrow abs" style="left:94px" width="16" height="24" viewBox="0 0 16 24"><path d="M14 1 L2 12 L14 23" fill="none" stroke="rgba(255,255,255,.45)" stroke-width="1.5"/></svg>
  <svg class="hero-arrow abs" style="left:648px" width="16" height="24" viewBox="0 0 16 24"><path d="M2 1 L14 12 L2 23" fill="none" stroke="rgba(255,255,255,.45)" stroke-width="1.5"/></svg>
</header>

<nav class="nav abs">
  <div class="brand abs"><i></i>BRAMBLEOAK</div>
  <ul class="menu abs">
    <li>HOME</li><li class="active">ABOUT</li><li>GALLERY</li><li>SERVICES</li><li>WARRANTY</li><li>CONTACT</li>
  </ul>
  <svg class="nav-pin abs" width="10" height="14" viewBox="0 0 10 14"><path d="M5 0 A5 5 0 0 1 10 5 C10 8 5 14 5 14 C5 14 0 8 0 5 A5 5 0 0 1 5 0Z" fill="#1e1c1c"/><circle cx="5" cy="5" r="1.8" fill="#fff"/></svg>
</nav>

<main>
  <div class="title-rule abs" style="left:214px;width:76px"></div>
  <div class="title-rule abs" style="left:467px;width:78px"></div>
  <h2 class="section-title abs">OUR SERVICES</h2>
  <p class="section-sub abs">The business has two sides to it.</p>

  <div class="worker abs" role="img" aria-label="Photo of a kneeling carpenter in a denim shirt marking a measuring tape"></div>

  <svg class="service-icon abs" style="left:154px;top:534px" viewBox="0 0 58 58"><circle cx="29" cy="29" r="28.5" fill="#fff" stroke="#555" stroke-width="1"/><path d="M20 41 L33 25 M30 19 L40 28 M28 22 L35 16 L43 24 L37 29" fill="none" stroke="#555" stroke-width="1.2" stroke-linejoin="round"/></svg>
  <svg class="service-icon abs" style="left:398px;top:534px" viewBox="0 0 58 58"><circle cx="29" cy="29" r="28.5" fill="#fff" stroke="#555" stroke-width="1"/><rect x="17" y="25" width="26" height="8" transform="rotate(40 30 29)" fill="none" stroke="#555" stroke-width="1.2"/><path d="M18 38 L34 19 L38 22 L22 41 L17 42Z" fill="none" stroke="#555" stroke-width="1.2"/></svg>

  <section class="service abs" style="left:227px;top:538px">
    <h2>One Side Provides</h2>
    <p>Lorem ipsum dolor sit amet, consectetur adipisicing elit, sed do eiusmod tempor incididunt ut labore et</p>
    <ul>
      <li><svg width="7" height="7" viewBox="0 0 8 8"><circle cx="4" cy="4" r="3.5" fill="none" stroke="#333" stroke-width=".8"/><path d="M2.3 4 L3.6 5.2 L5.8 2.8" fill="none" stroke="#333" stroke-width=".8"/></svg>Lorem ipsum dolor sit amet</li>
      <li><svg width="7" height="7" viewBox="0 0 8 8"><circle cx="4" cy="4" r="3.5" fill="none" stroke="#333" stroke-width=".8"/><path d="M2.3 4 L3.6 5.2 L5.8 2.8" fill="none" stroke="#333" stroke-width=".8"/></svg>Consectetur adipisicing elit sed</li>
      <li><svg width="7" height="7" viewBox="0 0 8 8"><circle cx="4" cy="4" r="3.5" fill="none" stroke="#333" stroke-width=".8"/><path d="M2.3 4 L3.6 5.2 L5.8 2.8" fill="none" stroke="#333" stroke-width=".8"/></svg>tempor incididunt ut labore</li>
      <li><svg width="7" height="7" viewBox="0 0 8 8"><circle cx="4" cy="4" r="3.5" fill="none" stroke="#333" stroke-width=".8"/><path d="M2.3 4 L3.6 5.2 L5.8 2.8" fill="none" stroke="#333" stroke-width=".8"/></svg>sed do eiusmod tempor incididunt labore et</li>
    </ul>
    <div class="btn" style="width:50px;margin-top:9px">Click Here</div>
  </section>

  <section class="service abs" style="left:469px;top:538px">
    <h2>Second Side Provides</h2>
    <p>Lorem ipsum dolor sit amet, consectetur adipisicing elit, sed do eiusmod tempor incididunt ut labore et</p>
    <ul>
      <li><svg width="7" height="7" viewBox="0 0 8 8"><circle cx="4" cy="4" r="3.5" fill="none" stroke="#333" stroke-width=".8"/><path d="M2.3 4 L3.6 5.2 L5.8 2.8" fill="none" stroke="#333" stroke-width=".8"/></svg>Lorem ipsum dolor sit amet</li>
      <li><svg width="7" height="7" viewBox="0 0 8 8"><circle cx="4" cy="4" r="3.5" fill="none" stroke="#333" stroke-width=".8"/><path d="M2.3 4 L3.6 5.2 L5.8 2.8" fill="none" stroke="#333" stroke-width=".8"/></svg>Consectetur adipisicing elit sed</li>
      <li><svg width="7" height="7" viewBox="0 0 8 8"><circle cx="4" cy="4" r="3.5" fill="none" stroke="#333" stroke-width=".8"/><path d="M2.3 4 L3.6 5.2 L5.8 2.8" fill="none" stroke="#333" stroke-width=".8"/></svg>tempor incididunt ut labore</li>
      <li><svg width="7" height="7" viewBox="0 0 8 8"><circle cx="4" cy="4" r="3.5" fill="none" stroke="#333" stroke-width=".8"/><path d="M2.3 4 L3.6 5.2 L5.8 2.8" fill="none" stroke="#333" stroke-width=".8"/></svg>sed do eiusmod tempor incididunt labore et</li>
    </ul>
    <div class="btn" style="width:50px;margin-top:9px">Click Here</div>
  </section>

  <section class="mission abs">
    <h3>Our Mission</h3>
    <p>Our passion is to deliver inspired cabinetry solutions to suit all your needs, supported by our phenomenal star class customer service</p>
  </section>
  <div class="btn abs" style="left:234px;top:893px;width:50px">Learn More</div>

  <div class="gallery abs">
    <div role="img" aria-label="Dark modern kitchen cabinets" style="background:linear-gradient(180deg,#1d1d1d,#3a3a3a 60%,#555)"></div>
    <div role="img" aria-label="Kitchen with green backsplash" style="background:linear-gradient(180deg,#2b2b2b,#4a5a3a 55%,#2a2a22)"></div>
    <div role="img" aria-label="Kitchen island with bar stools" style="background:linear-gradient(180deg,#3a2f28,#8a6a48 55%,#3c2e24)"></div>
    <div role="img" aria-label="Dining area with bright windows" style="background:linear-gradient(180deg,#cfc9bd,#8a7662 60%,#3c2f25)"></div>
    <div role="img" aria-label="Entertainment unit with television" style="background:linear-gradient(180deg,#2a2220,#4a3a35 50%,#c9b8a8)"></div>
    <div role="img" aria-label="Open kitchen with pendant lights" style="background:linear-gradient(180deg,#5a4a3e,#3a2e26 55%,#8a7a6a)"></div>
  </div>
  <div class="btn abs" style="left:475px;top:893px;width:50px">Click Here</div>
</main>

<footer class="footer abs">
  <svg class="pin" width="13" height="17" viewBox="0 0 10 14"><path d="M5 0 A5 5 0 0 1 10 5 C10 8 5 14 5 14 C5 14 0 8 0 5 A5 5 0 0 1 5 0Z" fill="#f15a22"/><circle cx="5" cy="5" r="1.8" fill="#282626"/></svg>
  <p class="addr">4120 Cedar Hollow Road, Maple Ridge, Alberta, T0X 1A0</p>
  <p class="tel">Tel: 555-010-4821 or 555-010-7734</p>
  <div class="social">
    <svg width="12" height="13" viewBox="0 0 28 30"><polygon points="14,1 27,8 27,22 14,29 1,22 1,8" fill="none" stroke="#bdbdbd" stroke-width="2"/></svg>
    <svg width="12" height="13" viewBox="0 0 28 30"><polygon points="14,1 27,8 27,22 14,29 1,22 1,8" fill="none" stroke="#bdbdbd" stroke-width="2"/></svg>
    <svg width="12" height="13" viewBox="0 0 28 30"><polygon points="14,1 27,8 27,22 14,29 1,22 1,8" fill="none" stroke="#bdbdbd" stroke-width="2"/></svg>
    <svg width="12" height="13" viewBox="0 0 28 30"><polygon points="14,1 27,8 27,22 14,29 1,22 1,8" fill="none" stroke="#bdbdbd" stroke-width="2"/></svg>
  </div>
  <p class="copy">© 2015</p>
  <div class="rule"></div>
  <ul class="footer-menu">
    <li>HOME</li><li>ABOUT</li><li>GALLERY</li><li>SERVICES</li><li>WARRANTY</li><li>CONTACT</li>
  </ul>
</footer>

</body>
</html>
```